Harrow Grading LLC business card design

Excavation company business cards

Contact Information for Business Card

Harrow Grading LLC cell phone 208-417-6290 office phone 208-319-4856 harrowgradingllc@maplecove.com Driveways, site prep, retaining walls, septic systems, rock delivery

Colors

Designer to choose colors to be used in the design.

```html
<!DOCTYPE html>
<html lang="en">
<head>
<meta charset="utf-8">
<title>Harrow Grading LLC — Business Card</title>
<link href="https://fonts.googleapis.com/css2?family=Roboto:wght@400;500;700&display=swap" rel="stylesheet">
<style>
  :root {
    --bg: #c9c9c9;
    --orange: #ea6d24;
    --white: #ffffff;
    --slate: #666666;
    --ink: #2b2b2b;
    --radius: 22px;
  }
  * { box-sizing: border-box; margin: 0; padding: 0; }
  html, body { width: 1200px; height: 788px; overflow: hidden; }
  body {
    background: var(--bg);
    font-family: "Roboto", Arial, sans-serif;
    display: flex;
    align-items: center;
    justify-content: center;
    gap: 60px;
  }
  .card {
    position: relative;
    width: 520px;
    height: 297px;
    border-radius: var(--radius);
    overflow: hidden;
    box-shadow: 0 10px 24px rgba(0,0,0,0.25);
  }

  /* Front */
  .card-front { background: var(--white); }
  .front-brand {
    position: absolute;
    top: 0; left: 0; right: 0;
    height: 160px;
    display: flex;
    align-items: center;
    justify-content: center;
    gap: 12px;
  }
  .brand-dot {
    width: 18px; height: 18px;
    border-radius: 50%;
    background: var(--orange);
    flex: none;
  }
  .brand-name {
    font-weight: 700;
    font-size: 30px;
    color: var(--orange);
    letter-spacing: 0.5px;
    white-space: nowrap;
  }
  .front-band {
    position: absolute;
    left: 0; right: 0; bottom: 0;
    height: 137px;
    background: var(--orange);
    color: var(--white);
    display: flex;
    align-items: center;
    padding: 0 24px 0 36px;
  }
  .person {
    display: flex;
    flex-direction: column;
    align-items: flex-end;
    width: 184px;
    flex: none;
  }
  .person-name { font-weight: 700; font-size: 21px; letter-spacing: 0.3px; white-space: nowrap; }
  .person-title { font-size: 16px; margin-top: 2px; }
  .band-divider {
    width: 1px;
    height: 78px;
    background: rgba(255,255,255,0.7);
    margin: 0 20px;
    flex: none;
  }
  .contact-list { list-style: none; font-size: 13.5px; line-height: 1.55; white-space: nowrap; }
  .contact-list li { display: flex; align-items: center; gap: 7px; }
  .contact-list svg { width: 12px; height: 12px; flex: none; }

  /* Back */
  .card-back { background: var(--slate); }
  .back-brand {
    position: absolute;
    top: 0; left: 0; right: 0;
    height: 228px;
    display: flex;
    align-items: center;
    justify-content: center;
    gap: 14px;
  }
  .back-brand .brand-name { color: var(--ink); font-size: 38px; }
  .back-brand .brand-dot { background: var(--ink); width: 22px; height: 22px; }
  .back-rule {
    position: absolute;
    left: 0; right: 0;
    top: 232px;
    height: 4px;
    background: var(--white);
  }
  .back-band {
    position: absolute;
    left: 0; right: 0; bottom: 0;
    height: 57px;
    background: var(--orange);
    color: var(--white);
    display: flex;
    align-items: center;
    justify-content: center;
    padding: 0 22px;
  }
  .services {
    font-size: 13px;
    font-weight: 500;
    letter-spacing: 0.1px;
    white-space: nowrap;
  }
  .services .sep { margin: 0 5px; }
</style>
</head>
<body>

  <section class="card card-front" aria-label="Business card front">
    <div class="front-brand">
      <span class="brand-dot"></span>
      <span class="brand-name">Harrow Grading LLC</span>
    </div>
    <div class="front-band">
      <div class="person">
        <span class="person-name">DANE WHITLOCK</span>
        <span class="person-title">Founder</span>
      </div>
      <span class="band-divider"></span>
      <ul class="contact-list">
        <li>
          <svg viewBox="0 0 24 24" fill="#fff"><path d="M6.6 10.8a15 15 0 0 0 6.6 6.6l2.2-2.2a1 1 0 0 1 1-.25 11.4 11.4 0 0 0 3.6.57 1 1 0 0 1 1 1V20a1 1 0 0 1-1 1A17 17 0 0 1 3 4a1 1 0 0 1 1-1h3.5a1 1 0 0 1 1 1c0 1.25.2 2.45.57 3.57a1 1 0 0 1-.25 1z"/></svg>
          208-319-4856
        </li>
        <li>
          <svg viewBox="0 0 24 24" fill="none" stroke="#fff" stroke-width="2.5"><rect x="6" y="2" width="12" height="20" rx="2"/><line x1="11" y1="18" x2="13" y2="18"/></svg>
          208-417-6290
        </li>
        <li>
          <svg viewBox="0 0 24 24" fill="none" stroke="#fff" stroke-width="2.5"><rect x="2" y="5" width="20" height="14" rx="1"/><polyline points="2,5 12,13 22,5"/></svg>
          harrowgradingllc@maplecove.com
        </li>
        <li>
          <svg viewBox="0 0 24 24" fill="none" stroke="#fff" stroke-width="2.5"><circle cx="12" cy="12" r="10"/><line x1="2" y1="12" x2="22" y2="12"/><ellipse cx="12" cy="12" rx="4" ry="10"/></svg>
          www.harrowgradingllc.com
        </li>
      </ul>
    </div>
  </section>

  <section class="card card-back" aria-label="Business card back">
    <div class="back-brand">
      <span class="brand-dot"></span>
      <span class="brand-name">Harrow Grading LLC</span>
    </div>
    <div class="back-rule"></div>
    <div class="back-band">
      <p class="services">Driveways<span class="sep">•</span>Site Prep<span class="sep">•</span>Retaining Walls<span class="sep">•</span>Septic Systems<span class="sep">•</span>Rock Delivery</p>
    </div>
  </section>

</body>
</html>
```